Telecommunications/Power civil contractor needs business card design

Were a new telecommunications/power underground civil contractor that is looking for a new business card design. Our company colours are silver or grey and orange. Feel free to use the white background logo or the black background logo.

Target Market(s)

Local contractors, utility companies, private sector mining/energy companies, developers.

Industry/Entity Type

Telecommunications

Contact Information for Business Card

Each card will need the following info:
Persons name:
Title:
E-mail:
Phone number:
Shop Address:
Mailing Address:

Requirements
Must have
• Each card will need the following info:
• Persons name:
• Title:
• E-mail:
• Phone number:
• Shop Address:
• Mailing Address:

```html
<!DOCTYPE html>
<html lang="en">
<head>
<meta charset="utf-8">
<title>Ridgeview Civil Inc – Business Card</title>
<link rel="stylesheet" href="https://fonts.googleapis.com/css2?family=Montserrat:wght@800&family=Libre+Baskerville&family=Open+Sans:wght@400&family=Arimo&family=Didact+Gothic&display=swap">
<style>
  :root {
    --page: #d9d4cf;
    --card: #ecebe8;
    --orange: #e0492c;
    --orange-deep: #c93a22;
    --charcoal: #3a3836;
    --ink: #2f2d2b;
    --contact-text: #d8d2ca;
    --icon-tile: #c7a98b;
    --notch: #6e6a66;
  }
  * { margin: 0; padding: 0; box-sizing: border-box; }
  html, body { width: 1200px; height: 970px; overflow: hidden; }
  body { background: var(--page); position: relative; }

  .card {
    position: absolute; left: 185px; top: 235px;
    width: 830px; height: 500px;
    background: var(--card);
    border-radius: 22px;
    overflow: hidden;
    box-shadow: 0 10px 30px rgba(0,0,0,0.15);
  }

  .brand { position: absolute; left: 0; right: 0; top: 30px; text-align: center; }
  .brand-mark {
    width: 120px; height: 120px; margin: 0 auto;
    border-radius: 50%; border: 7px solid var(--orange);
  }
  .brand-name {
    margin-top: 26px;
    font-family: "Montserrat", sans-serif; font-weight: 800;
    font-size: 36px; letter-spacing: 1px; color: var(--orange);
  }

  .band { position: absolute; left: 0; right: 0; top: 284px; height: 169px; display: flex; }
  .band-person {
    position: relative; width: 429px; height: 100%;
    background: linear-gradient(90deg, var(--orange-deep), var(--orange));
    padding: 58px 0 0 90px;
  }
  .band-person::before {
    content: ""; position: absolute; left: 180px; top: 0;
    border-left: 20px solid transparent; border-right: 20px solid transparent;
    border-top: 16px solid var(--notch);
  }
  .band-person::after {
    content: ""; position: absolute; right: -18px; top: 18px;
    border-top: 18px solid transparent; border-bottom: 18px solid transparent;
    border-left: 18px solid var(--orange);
    z-index: 2;
  }
  .person-name { font-family: "Libre Baskerville", serif; font-size: 25px; color: #f6ece6; }
  .person-title { margin-top: 6px; font-family: "Open Sans", sans-serif; font-size: 19px; color: var(--ink); }

  .band-contact { flex: 1; background: var(--charcoal); padding: 18px 0 0 50px; }
  .contact-row { display: flex; align-items: flex-start; margin-bottom: 18px; }
  .contact-icon {
    width: 26px; height: 26px; border-radius: 4px; background: var(--icon-tile);
    flex: none; margin-right: 36px; display: flex; align-items: center; justify-content: center;
  }
  .contact-text { font-family: "Arimo", sans-serif; font-size: 17px; line-height: 22px; color: var(--contact-text); }

  .email {
    position: absolute; left: 0; right: 0; top: 463px; text-align: center;
    font-family: "Didact Gothic", sans-serif; font-size: 19px; letter-spacing: 1.5px; color: var(--ink);
  }
  .email .domain { color: var(--orange); }
</style>
</head>
<body>
  <div class="card">
    <div class="brand">
      <div class="brand-mark"></div>
      <div class="brand-name">RIDGEVIEW CIVIL INC</div>
    </div>

    <div class="band">
      <div class="band-person">
        <div class="person-name">Marco L Reyes</div>
        <div class="person-title">Managing Partner</div>
      </div>
      <div class="band-contact">
        <div class="contact-row">
          <span class="contact-icon">
            <svg width="16" height="16" viewBox="0 0 16 16" aria-hidden="true">
              <rect x="4" y="1" width="8" height="4" fill="#3a3836"/>
              <rect x="1" y="5" width="14" height="6" rx="1" fill="#3a3836"/>
              <rect x="4" y="9" width="8" height="6" fill="#3a3836" stroke="#c7a98b" stroke-width="1"/>
            </svg>
          </span>
          <span class="contact-text">+1 (555) 014-2290</span>
        </div>
        <div class="contact-row">
          <span class="contact-icon">
            <svg width="16" height="16" viewBox="0 0 16 16" aria-hidden="true">
              <path d="M8 1 L15 8 H13 V15 H9.5 V10.5 H6.5 V15 H3 V8 H1 Z" fill="#3a3836"/>
            </svg>
          </span>
          <span class="contact-text">Unit 42, Block 7, Harlow</span>
        </div>
        <div class="contact-row">
          <span class="contact-icon">
            <svg width="16" height="16" viewBox="0 0 16 16" aria-hidden="true">
              <path d="M8 1 L15 8 H13 V15 H9.5 V10.5 H6.5 V15 H3 V8 H1 Z" fill="#3a3836"/>
            </svg>
          </span>
          <span class="contact-text">18 Maple Row, 2nd Floor,<br>Fairview, OR 97024</span>
        </div>
      </div>
    </div>

    <div class="email">care@<span class="domain">ridgeviewcivilinc</span>.com</div>
  </div>
</body>
</html>
```